Business Card Update, need to bring life to the card, two sided color

We need a new business card design, are moving and changing addresses and need a new look, we have the logos already attached but need a new style moving forward. Can incorporate the color of the logo (The Green) as well, maybe a solid back? We deal with safety products revolving around static electricity and safety lighting. Would like to keep same font in second logo as well.

Target Market(s)

Electrical Safety, Lighting

Contact Information for Business Card

Dale Fenwick
Vice President
Office: 770-555-4821
Cell: 770-555-3067
dale@tkfenwick.example
www.tkfenwick.example
4700 West Harbor Boulevard
Suite #150
Roswell, GA 30076

Font styles to use
Serif
Sans Serif

Requirements
Must have
• Since 1918
Nice to have
• Could use the 100 Year Logo for back of card, would like the back of card to be the same green as logo.
Should not have
• No black cards please.

```html
<!DOCTYPE html>
<html lang="en">
<head>
<meta charset="utf-8">
<title>T.K. Fenwick – Business Card</title>
<link href="https://fonts.googleapis.com/css2?family=Roboto:wght@400;500;700;900&display=swap" rel="stylesheet">
<style>
  :root {
    --brand-green: #06985c;
    --paper-white: #ffffff;
    --backdrop: #e6e8e7;
    --card-radius: 22px;
  }
  * { box-sizing: border-box; margin: 0; padding: 0; }
  html, body {
    width: 1200px; height: 768px; overflow: hidden;
    background: var(--backdrop);
    font-family: "Roboto", Arial, sans-serif;
  }
  .canvas { position: relative; width: 1200px; height: 768px; }
  .card {
    position: absolute; top: 229px;
    width: 540px; height: 310px;
    border-radius: var(--card-radius);
    overflow: hidden;
    box-shadow: 0 10px 30px rgba(0,0,0,0.18);
  }
  /* Back side */
  .card-back { left: 40px; background: var(--brand-green); color: var(--paper-white); }
  .back-mark {
    position: absolute; left: 50%; top: 44%;
    transform: translate(-50%, -50%);
    display: flex; flex-direction: column; align-items: center; gap: 12px;
  }
  .back-mark .mark-dot {
    width: 84px; height: 84px; border-radius: 50%;
    background: var(--paper-white);
  }
  .back-mark .mark-name {
    font-weight: 700; font-size: 20px; letter-spacing: 2px;
    color: var(--paper-white);
  }
  .back-url {
    position: absolute; left: 0; right: 0; bottom: 36px;
    text-align: center; font-size: 12px; letter-spacing: 5px;
    color: var(--paper-white);
  }
  /* Front side */
  .card-front { left: 620px; background: var(--paper-white); }
  .contact-disc {
    position: absolute; left: 258px; top: -12px;
    width: 350px; height: 350px; border-radius: 50%;
    background: var(--brand-green);
  }
  .company-block {
    position: absolute; left: 24px; top: 56px; width: 230px;
    display: flex; flex-direction: column; align-items: center;
    color: var(--brand-green);
  }
  .company-block .mark-dot {
    width: 66px; height: 66px; border-radius: 50%;
    background: var(--brand-green); margin-bottom: 12px;
  }
  .company-name { font-weight: 900; font-size: 29px; line-height: 1; white-space: nowrap; }
  .company-tagline { font-weight: 700; font-size: 11.5px; margin-top: 5px; white-space: nowrap; }
  .company-since {
    font-weight: 700; font-size: 11.5px; margin-top: 6px;
    letter-spacing: 2px; text-transform: uppercase; white-space: nowrap;
  }
  .contact-block {
    position: absolute; left: 312px; top: 44px;
    color: var(--paper-white);
  }
  .person-name { font-weight: 700; font-size: 20px; line-height: 1.05; }
  .person-title { font-size: 12px; margin-bottom: 9px; }
  .address { font-size: 11.5px; line-height: 1.3; margin-bottom: 8px; }
  .contact-list { list-style: none; font-size: 11.5px; line-height: 1.45; }
  .contact-list li { display: flex; align-items: center; gap: 7px; white-space: nowrap; }
  .contact-list svg { width: 11px; height: 11px; flex: none; fill: var(--paper-white); }
</style>
</head>
<body>
<main class="canvas">
  <section class="card card-back" aria-label="Card back">
    <div class="back-mark">
      <span class="mark-dot"></span>
      <span class="mark-name">T.K. FENWICK</span>
    </div>
    <p class="back-url">www.tkfenwick.example</p>
  </section>

  <section class="card card-front" aria-label="Card front">
    <div class="contact-disc"></div>
    <div class="company-block">
      <span class="mark-dot"></span>
      <p class="company-name">T.K. Fenwick</p>
      <p class="company-tagline">Manufacturing Company, Inc.</p>
      <p class="company-since">Since 1918</p>
    </div>
    <div class="contact-block">
      <p class="person-name">Dale Fenwick</p>
      <p class="person-title">Vice President</p>
      <p class="address">4700 West Harbor Boulevard<br>Suite #150<br>Roswell, GA 30076</p>
      <ul class="contact-list">
        <li><svg viewBox="0 0 12 12"><path d="M2.5 0.5l2 2.5-1.2 1.3c.7 1.6 2 2.9 3.5 3.6L8 6.6l2.6 2-1 2.4C5 11 1 7 .6 2z"/></svg>770 555 4821</li>
        <li><svg viewBox="0 0 12 12"><path d="M3 0h6v12H3zM4 1.5v8h4v-8z"/></svg>770 555 3067</li>
        <li><svg viewBox="0 0 12 12"><path d="M0 2h12v1L6 7 0 3zM0 4.5l6 4 6-4V10H0z"/></svg>dale@tkfenwick.example</li>
        <li><svg viewBox="0 0 12 12"><circle cx="6" cy="6" r="6"/></svg>www.tkfenwick.example</li>
      </ul>
    </div>
  </section>
</main>
</body>
</html>
```